Modern Business Card for Larkwell 2018

Our company assumes the best about people. We are creating an online community of entrepreneurs and business leaders who struggle with marketing their business online.

This business card should POP! We recently got a new logo and are launching a new website next month, so our business cards should make a statement that feels:
-Fresh
-Smart
-Trustworthy
-Fun

Target Market(s)

small business owners, entrepreneurs

Industry/Entity Type

Digital Marketing

Contact Information for Business Card

Dimensions: 3.5" x 2"

Font styles to use
Sans Serif

Colors
f37122
ffffff

Requirements
Must have
• We need a business card with a modern, bold design. We will use one side of the card as a lead-generation offer, so text on one side will need to fit up to 140 characters. The business card should stick to our core colors (orange, black, and white).
Nice to have
• We think a vertical "portrait" design could be interesting.
Should not have
• Should not look like a traditional business card. The round icon should stand out from a distance.

```html
<!DOCTYPE html>
<html lang="en">
<head>
<meta charset="utf-8">
<title>Larkwell Business Card</title>
<link rel="stylesheet" href="https://fonts.googleapis.com/css2?family=Roboto:wght@400;500;700&family=Montserrat:wght@700&family=Caveat:wght@500&family=Permanent+Marker&display=swap">
<style>
  :root {
    --orange: #f37122;
    --orange-deep: #f0661c;
    --orange-soft: #f47d36;
    --white: #ffffff;
    --card-white: #f4f4f4;
    --ink: #222222;
    --backdrop: #5e4332;
  }
  * { box-sizing: border-box; margin: 0; padding: 0; }
  html, body { width: 1200px; height: 960px; overflow: hidden; }
  body { background: var(--backdrop); font-family: "Roboto", Arial, sans-serif; position: relative; }

  .card {
    position: absolute; width: 600px; height: 343px;
    border-radius: 22px; overflow: hidden; background: var(--card-white);
    box-shadow: 0 4px 10px rgba(0,0,0,.35);
  }
  .card--front { left: 314px; top: 113px; }
  .card--back { left: 311px; top: 472px; }

  /* Front */
  .front-mark { position: absolute; left: 58px; top: 60px; display: flex; align-items: center; gap: 14px; }
  .front-mark__dot { width: 60px; height: 60px; border-radius: 50%; background: var(--orange); }
  .front-mark__name { font-family: "Montserrat", Arial, sans-serif; font-weight: 700; font-size: 30px; color: var(--orange); letter-spacing: 1px; }
  .front-disc { position: absolute; left: 0; top: 0; }
  .contact { position: absolute; right: 36px; top: 184px; text-align: right; color: var(--white); }
  .contact__role { font-size: 16px; letter-spacing: .3px; }
  .contact__name { font-family: "Caveat", cursive; font-weight: 500; font-size: 46px; line-height: 1; margin-top: 10px; text-transform: uppercase; }
  .contact__email { font-size: 15px; font-weight: 500; margin-top: 14px; }

  /* Back */
  .offer-band { position: absolute; left: 0; top: 0; width: 600px; height: 218px; background: var(--orange); }
  .brand { position: absolute; left: 40px; top: 58px; width: 240px; text-align: center; color: var(--white); }
  .brand__dot { width: 36px; height: 36px; border-radius: 50%; background: var(--white); margin: 0 auto 10px; }
  .brand__name { font-family: "Montserrat", Arial, sans-serif; font-weight: 700; font-size: 34px; line-height: 1; letter-spacing: .5px; }
  .brand__tagline { font-family: "Permanent Marker", cursive; font-size: 12px; margin-top: 6px; letter-spacing: .6px; }
  .divider { position: absolute; left: 297px; top: 28px; width: 1px; height: 166px; background: rgba(255,255,255,.6); }
  .offer { position: absolute; left: 323px; top: 30px; color: var(--white); }
  .offer__headline { font-weight: 700; font-size: 19px; line-height: 21px; text-transform: uppercase; }
  .offer__body { font-size: 15px; line-height: 20px; margin-top: 6px; }
  .offer__link { font-weight: 700; font-size: 19px; margin-top: 9px; }
  .note-line { position: absolute; left: 36px; width: 520px; height: 1px; background: var(--ink); }
  .note-line--one { top: 260px; }
  .note-line--two { top: 300px; }
</style>
</head>
<body>
  <section class="card card--front">
    <svg class="front-disc" width="600" height="343" aria-hidden="true">
      <circle cx="431" cy="272" r="172" fill="var(--orange-deep)"/>
      <circle cx="431" cy="272" r="163" fill="var(--orange-soft)"/>
    </svg>
    <div class="front-mark">
      <span class="front-mark__dot"></span>
      <span class="front-mark__name">LARKWELL</span>
    </div>
    <div class="contact">
      <p class="contact__role">STORY MARKETING COACH</p>
      <p class="contact__name">Nora Bexley</p>
      <p class="contact__email">nora@larkwellnow.com</p>
    </div>
  </section>

  <section class="card card--back">
    <div class="offer-band">
      <div class="brand">
        <div class="brand__dot"></div>
        <p class="brand__name">LARKWELL</p>
        <p class="brand__tagline">TELL STORIES THAT INSPIRE ACTION</p>
      </div>
      <div class="divider"></div>
      <div class="offer">
        <p class="offer__headline">Reach more people.<br>Make more money.<br>Create more impact.</p>
        <p class="offer__body">Get your free Larkwell<br>Starter Package and our<br>marketing guide today at</p>
        <p class="offer__link">Larkwellnow.com/start</p>
      </div>
    </div>
    <div class="note-line note-line--one"></div>
    <div class="note-line note-line--two"></div>
  </section>
</body>
</html>
```